Agriculture farming Hemp and CBD

The logo is in works with your company now, should be ready in a few days. We have our Domain (kestrelbrookhollow.com) We would like to see incorporated seed to growth, but not necessary. we would like to nature colors and some black and green. we have our farm and will be growing and selling HEMP and CBD we are based in the state of Virginia. Would like to incorporate the words pause, play, rewind if possible but not necessary.

Target Market(s)

20 years old to elderly

Coding

Coded - Design and coding required

Number of Pages Required

3 page

Font styles to use
Serif

Requirements
Must have
• I'm not sure on the must haves, we are open to any ideas, we would definitely like to see Hemp and CBD included, may the life cycle of seed to plant. We must have a pop up asking if you are 20 years old before they can enter our site and to view or purchase our product. I want the design to be totally different than what i uploaded.
Nice to have
• Would like to see natural colors as well as black and green
Should not have
• I want

```html
<!DOCTYPE html>
<html lang="en">
<head>
<meta charset="utf-8">
<title>Kestrel Brook Hollow — Age Check</title>
<link rel="stylesheet" href="https://fonts.googleapis.com/css2?family=Open+Sans:wght@400;600;700&display=swap">
<style>
:root{
  --page-dark:#0c0d0b;
  --hero-a:#2a2d22;
  --hero-b:#14150f;
  --band:#8a8a8a;
  --green:#21b021;
  --green-soft:#1fa51f;
  --white:#ffffff;
  --overlay:rgba(0,0,0,.62);
  --modal:#ececec;
  --modal-line:#dcdcdc;
  --ink:#3a3a3a;
  --yes:#00d836;
  --yes-ring:#70e08a;
  --no:#ff0000;
  --no-ring:#f07070;
}
*{box-sizing:border-box;margin:0;padding:0}
html,body{width:1200px;height:985px;overflow:hidden;background:var(--page-dark);font-family:'Open Sans',sans-serif}
.site{position:relative;width:1200px;height:985px}
.hero{position:absolute;left:0;top:0;width:1200px;height:687px;
  background:radial-gradient(ellipse at 35% 35%,#4b4d3c 0%,var(--hero-a) 30%,var(--hero-b) 70%),var(--hero-b)}
.hero-plant{position:absolute;left:620px;top:150px;width:580px;height:537px;
  background:radial-gradient(ellipse at 50% 55%,#5e4a2c 0%,#33301f 45%,rgba(20,21,15,0) 75%)}
.header{position:absolute;left:0;top:0;width:1200px;height:170px}
.social{position:absolute;left:78px;top:54px;display:flex;gap:19px}
.social span{width:16px;height:16px;border-radius:50%;background:#d8d8d8}
.brand{position:absolute;left:0;width:1200px;top:38px;text-align:center;font-size:24px;font-weight:600;color:var(--green)}
.tools{position:absolute;left:1005px;top:50px;display:flex;gap:18px;align-items:center}
.nav{position:absolute;left:243px;top:122px;width:712px;height:44px;border-bottom:2px solid var(--green-soft)}
.nav a{position:absolute;top:0;transform:translateX(-50%);font-size:16px;font-weight:600;color:var(--white);text-decoration:none;white-space:nowrap}
.hero-title{position:absolute;left:151px;top:325px;border-left:4px solid var(--green);padding-left:28px;height:156px}
.hero-title p{font-size:48px;font-weight:700;line-height:61px;color:#e8e8e8;margin-top:-8px}
.hero-title p.accent{color:var(--green);font-size:42px}
.about{position:absolute;left:0;top:687px;width:1200px;height:298px;background:var(--band)}
.about-photo{position:absolute;left:70px;top:60px;width:440px;height:238px;
  background:radial-gradient(ellipse at 50% 50%,#3b3226 0%,#6e6a4a 45%,rgba(138,138,138,0) 80%)}
.about h2{position:absolute;left:639px;top:152px;font-size:32px;font-weight:700;color:var(--green)}
.about p{position:absolute;left:637px;top:218px;width:391px;font-size:13px;line-height:19px;color:#f4f4f4;letter-spacing:-.3px}
.overlay{position:absolute;inset:0;background:var(--overlay)}
.age-modal{position:absolute;left:344px;top:265px;width:512px;height:438px;background:var(--modal);border-radius:19px}
.age-modal::before{content:"";position:absolute;inset:10px;border:1px solid var(--modal-line);border-radius:14px}
.age-question{position:absolute;left:0;top:58px;width:512px;text-align:center;font-size:32px;font-weight:700;line-height:38px;color:var(--ink)}
.choice{position:absolute;top:199px;width:132px;text-align:center}
.choice.yes{left:100px}
.choice.no{left:280px}
.choice .ring{width:132px;height:132px;border-radius:50%;display:flex;align-items:center;justify-content:center}
.yes .ring{background:var(--yes);border:6px solid var(--yes-ring)}
.no .ring{background:var(--no);border:6px solid var(--no-ring)}
.choice .label{margin-top:8px;font-size:26px;font-weight:700;color:var(--ink)}
</style>
</head>
<body>
<div class="site">
  <section class="hero">
    <div class="hero-plant" role="img" aria-label="Flowering hemp plant photograph"></div>
    <header class="header">
      <div class="social"><span></span><span></span><span></span><span></span></div>
      <div class="brand">kestrelbrookhollow.com</div>
      <div class="tools">
        <svg width="24" height="24" viewBox="0 0 24 24" fill="none" stroke="#e6e6e6" stroke-width="2.4"><circle cx="10" cy="10" r="7"/><path d="M15 15l6 6"/></svg>
        <svg width="22" height="24" viewBox="0 0 22 24" fill="none" stroke="#e6e6e6" stroke-width="2.2"><path d="M3 9h16l-1 13H4z"/><path d="M7 9V6a4 4 0 0 1 8 0v3"/></svg>
        <svg width="22" height="20" viewBox="0 0 22 20" fill="var(--green)"><rect y="2" width="22" height="3"/><rect y="8.5" width="22" height="3"/><rect y="15" width="22" height="3"/></svg>
      </div>
      <nav class="nav">
        <a style="left:68px">Home</a>
        <a style="left:177px">About ⌄</a>
        <a style="left:298px">Products ⌄</a>
        <a style="left:417px">Blogs</a>
        <a style="left:521px">Shop ⌄</a>
        <a style="left:636px">Contact</a>
      </nav>
    </header>
    <div class="hero-title">
      <p class="accent">VIRGINIA GROWTH</p>
      <p>EXPERTISE IN HEMP</p>
      <p>CULTIVATION</p>
    </div>
  </section>
  <section class="about">
    <div class="about-photo" role="img" aria-label="CBD oil dropper bottles with a hemp leaf"></div>
    <h2>ABOUT US</h2>
    <p>we have our farm and will be growing and selling HEMP and CBD we are based in the state of Virginia. Would like to incorporate the words pause, play, rewind if possible but not necessary we have our farm and will be</p>
  </section>
  <div class="overlay"></div>
  <div class="age-modal" role="dialog" aria-label="Age verification">
    <h1 class="age-question">Are you atleast 21 to<br>enter this site?</h1>
    <div class="choice yes">
      <div class="ring">
        <svg width="60" height="60" viewBox="0 0 60 60" fill="#fff"><path d="M28 6h20v44l-16 5V50h-4v-8h4V18h-4z"/><path d="M4 28h14v-6l10 8-10 8v-6H4z"/></svg>
      </div>
      <div class="label">Yes</div>
    </div>
    <div class="choice no">
      <div class="ring">
        <svg width="60" height="60" viewBox="0 0 60 60" fill="#fff"><path d="M6 6h22v12h-4v-8h-4v38l-14 5z"/><path d="M24 42h4v8h-4z"/><path d="M28 26h16v-6l10 8-10 8v-6H28z"/></svg>
      </div>
      <div class="label">No</div>
    </div>
  </div>
</div>
</body>
</html>
```